BorrowNest Website design, we are a home loan / lending company

We are a finance broking company that can do mortgages / home loans, Car Loans, Commercial Loans, SMSF Loans, Business Loans, Personal Loans
We are looking for a simple website, not too busy, easy to navigate, something that prompts customers to action or call us.
I like the simplicity of the following websites:
https://www.velkarafinance.com.au/ - I like this website front page. I was thinking I have my logo, the one with the black background appear , then the toolbar at the top perhaps?
https://trevix.com.au/business-loans# - on this page there are images under finance that works for you that I like that concept.
https://dunmerel.com.au/contact/ - I like the Make an Appointment page
https://trevix.com.au/about-us - Simple but effective page design

Target Market(s)

Home Loan Customer

Industry/Entity Type

Finance / Home Loans

Coding

Coded - Design and coding required

Number of Pages Required

5+ page

Font styles to use
Serif

Colors
0094D4
00A9DD
6FCCEA
C7EBF8
E9F6FB

Requirements
Must have
• The following Heading s - Contact Us, About Us, Our People, Make an Appointment, Loan Options, Calculators, Reviews. I want to use the Logo colours I have in the zip files I uploaded.
Nice to have
• Simple clean design

```html
<!DOCTYPE html>
<html lang="en">
<head>
<meta charset="utf-8">
<title>BorrowNest – Home Loans & Lending</title>
<link rel="stylesheet" href="https://fonts.googleapis.com/css2?family=Merriweather:wght@700;900&family=Montserrat:wght@400;500;600;700;800&display=swap">
<style>
:root{
  --blue:#1b84d0;
  --blue-dark:#1570b8;
  --cyan:#16c3ef;
  --sky:#6fccea;
  --ice:#e9f6fb;
  --ink:#222;
  --text:#555;
  --grey-bg:#f1f1f1;
  --nav:#333;
  --footer:#0b0b0b;
  --white:#fff;
}
*{box-sizing:border-box;margin:0;padding:0}
html,body{width:1200px;height:4525px;overflow:hidden}
body{position:relative;background:var(--white);font-family:"Montserrat",sans-serif;color:var(--ink)}
.abs{position:absolute}
.serif-title{font-family:"Merriweather",serif;font-weight:700;color:var(--blue);letter-spacing:.5px}
.underline{display:block;width:62px;height:4px;background:var(--blue)}
.photo{position:absolute}
.brand{font-family:"Montserrat",sans-serif;font-weight:700}
/* header */
.topbar{left:0;top:0;width:1200px;height:63px;background:var(--white);border-top:3px solid var(--cyan)}
.topbar .brand{left:110px;top:6px;font-size:38px;color:#333;letter-spacing:-1px}
.social-dots{left:575px;top:24px;display:flex;gap:14px}
.social-dots span{width:11px;height:11px;border-radius:50%;background:var(--blue)}
.contact-chip{top:14px;display:flex;align-items:center;gap:8px}
.chip-icon{width:30px;height:30px;border-radius:50%;background:var(--blue);display:flex;align-items:center;justify-content:center}
.chip-label{font-size:9px;color:#888}
.chip-value{font-size:12.5px;color:#444}
.sep{top:26px;width:1px;height:12px;background:#aaa}
.nav{left:0;top:63px;width:1200px;height:45px;background:var(--nav)}
.nav a{position:absolute;top:15px;font-size:12.5px;font-weight:500;color:#fff;text-decoration:none}
.nav a.active{color:var(--cyan)}
/* hero */
.hero{left:0;top:108px;width:1200px;height:622px;overflow:hidden}
.hero-photo{left:0;top:0;width:1200px;height:622px;background:linear-gradient(160deg,#7f95a8 0%,#4d6273 45%,#6c7c88 70%,#3f4f5c 100%)}
.hero-panel{left:0;top:133px;width:590px;height:168px;background:rgba(60,70,80,.55);clip-path:polygon(0 0,100% 0,88% 100%,0 100%)}
.hero-title{left:108px;top:150px;font-size:62px;font-weight:800;color:#fff;letter-spacing:-1px}
.hero-title span{color:var(--cyan)}
.hero-sub{left:110px;top:234px;font-size:22px;color:#fff;font-weight:500}
.btn{display:flex;align-items:center;gap:14px;color:#fff;font-weight:600;text-decoration:none;background:var(--blue)}
.btn .arrow{width:30px;height:30px;border-radius:50%;background:#fff;display:flex;align-items:center;justify-content:center}
.hero-btn{left:110px;top:282px;width:170px;height:42px;padding-left:20px;font-size:13px}
.slide-arrow{width:64px;height:64px;border-radius:50%;border:2px solid rgba(255,255,255,.7);display:flex;align-items:center;justify-content:center}
.dots{left:573px;top:561px;display:flex;gap:8px}
.dots span{width:11px;height:11px;border-radius:50%;border:1.5px solid #fff}
.dots span.on{background:var(--cyan);border-color:var(--cyan)}
/* about */
.about-photo{left:138px;top:818px;width:400px;height:330px;background:linear-gradient(135deg,#4a5560,#8a8f92 50%,#3b3f45)}
.about-tab{left:500px;top:818px;width:70px;height:40px;background:#e6e6e6;clip-path:polygon(0 0,100% 0,0 100%)}
.lead{font-size:19px;font-weight:500;line-height:1.6;color:#2a2a2a}
.body{font-size:13.5px;line-height:1.9;color:var(--text)}
.ticks{list-style:none}
.ticks li{font-size:12.5px;font-weight:600;color:#333;display:flex;align-items:center;gap:16px;height:27px}
.ticks li::before{content:"";width:11px;height:11px;border-radius:50%;background:var(--cyan);box-shadow:inset 0 0 0 3px var(--cyan),inset 0 0 0 5px #fff}
/* services */
.services{left:0;top:1236px;width:1200px;height:990px;background:var(--grey-bg)}
.card{position:absolute;width:308px;height:346px;background:#fff;border-radius:6px;box-shadow:0 4px 14px rgba(0,0,0,.12);overflow:hidden;text-align:center}
.card .card-photo{height:190px}
.card .icon{position:absolute;left:123px;top:164px;width:62px;height:62px;border-radius:50%;background:var(--blue);border:3px solid #fff;display:flex;align-items:center;justify-content:center}
.card h3{margin-top:50px;font-size:19px;font-weight:500;color:#222}
.card p{margin:10px 18px 0;font-size:12px;line-height:1.85;color:#666}
.card .more{display:inline-flex;align-items:center;gap:28px;margin-top:10px;font-size:12.5px;color:var(--blue);text-decoration:underline;font-style:italic}
.mini-arrow{width:24px;height:24px;border-radius:50%;background:var(--blue);display:inline-flex;align-items:center;justify-content:center}
/* blog */
.post{position:absolute;width:433px;height:410px;background:#fff;box-shadow:0 4px 14px rgba(0,0,0,.14);padding:8px}
.post-photo{height:208px}
.post h3{margin:18px 10px 0;font-size:19px;font-weight:600;line-height:1.4;color:#222}
.post p{margin:12px 10px 0;font-size:14px;line-height:1.6;color:#555}
.post .date{margin:8px 10px 0;font-size:11.5px;color:var(--blue)}
.post .btn{margin:12px 10px 0;width:140px;height:34px;padding-left:16px;font-size:13px;gap:26px;background:var(--blue)}
.circle-nav{width:58px;height:58px;border-radius:50%;border:2px solid #1a4f86;display:flex;align-items:center;justify-content:center;background:#fff}
/* contact */
.contact{left:0;top:3436px;width:1200px;height:760px;background:linear-gradient(180deg,#f8f8f8 0%,#f6f7f8 60%,#e4ebf0 100%)}
.contact-photo{left:0;top:3950px;width:1200px;height:180px;background:linear-gradient(180deg,rgba(230,236,240,0) 0%,#d9e1e7 60%,#c8d2da 100%)}
.field{position:absolute;background:#fff;border:1.5px solid var(--blue);display:flex;align-items:center;gap:10px;padding-left:14px;font-size:11.5px;color:#555;letter-spacing:.3px}
.field.msg{align-items:flex-start;padding-top:14px}
.submit{left:532px;top:4020px;width:128px;height:42px;padding-left:20px;font-size:13px;gap:20px;background:var(--blue)}
/* footer */
.footer{left:0;top:4192px;width:1200px;height:333px;background:var(--footer);color:#fff}
.footer .brand{position:absolute;left:110px;top:72px;font-size:36px;color:#fff;letter-spacing:-1px}
.fcol{position:absolute;top:30px}
.fcol h4{font-size:15.5px;font-weight:700;letter-spacing:.3px}
.fcol .bar{display:block;width:36px;height:3px;background:var(--blue);margin:8px 0 18px}
.fcol a{display:block;font-size:12px;color:#ddd;text-decoration:none;line-height:26px;padding-left:6px}
.finfo{display:flex;gap:12px;margin-bottom:14px;font-size:12px;line-height:1.4}
.finfo small{display:block;font-size:11px;color:#aaa}
.fsocial{position:absolute;left:155px;top:194px;display:flex;gap:8px}
.fsocial span{width:33px;height:33px;border-radius:50%;border:1.5px solid #fff}
.fline{position:absolute;left:110px;top:278px;width:980px;height:1px;background:#444}
.copy{position:absolute;left:0;width:1200px;top:296px;text-align:center;font-size:12.5px;color:#ddd}
.to-top{position:absolute;left:1112px;top:224px;width:44px;height:44px;border-radius:50%;background:var(--blue);display:flex;align-items:center;justify-content:center}
</style>
</head>
<body>

<!-- Header -->
<header class="abs topbar">
  <div class="abs brand">BorrowNest</div>
  <div class="abs social-dots"><span></span><span></span><span></span></div>
  <div class="abs sep" style="left:677px"></div>
  <div class="abs contact-chip" style="left:700px">
    <div class="chip-icon"><svg width="14" height="10" viewBox="0 0 14 10"><rect x=".5" y=".5" width="13" height="9" fill="none" stroke="#fff"/><path d="M.5 .5 7 6l6.5-5.5" fill="none" stroke="#fff"/></svg></div>
    <div><div class="chip-label">Email</div><div class="chip-value">hello@borrownest.mail</div></div>
  </div>
  <div class="abs sep" style="left:915px"></div>
  <div class="abs contact-chip" style="left:940px">
    <div class="chip-icon"><svg width="14" height="14" viewBox="0 0 24 24"><path fill="#fff" d="M6.6 10.8a15 15 0 0 0 6.6 6.6l2.2-2.2c.3-.3.7-.4 1-.2 1.1.4 2.3.6 3.6.6.6 0 1 .4 1 1V20c0 .6-.4 1-1 1A17 17 0 0 1 3 4c0-.6.4-1 1-1h3.5c.6 0 1 .4 1 1 0 1.3.2 2.5.6 3.6.1.3 0 .7-.2 1z"/></svg></div>
    <div><div class="chip-label">Call or Text</div><div class="chip-value">+1 (555) 204 7719</div></div>
  </div>
</header>

<nav class="abs nav">
  <a class="active" style="left:175px" href="#">Home</a>
  <a style="left:251px" href="#">Contact Us</a>
  <a style="left:359px" href="#">About Us</a>
  <a style="left:456px" href="#">Our People</a>
  <a style="left:566px" href="#">Make an Appointment</a>
  <a style="left:742px" href="#">Loan Options</a>
  <a style="left:864px" href="#">Calculators</a>
  <a style="left:972px" href="#">Reviews</a>
</nav>

<!-- Hero -->
<section class="abs hero">
  <div class="photo hero-photo" role="img" aria-label="Two colleagues reviewing a laptop at a glass meeting table in a modern office"></div>
  <div class="abs hero-panel"></div>
  <h1 class="abs hero-title">Borrow<span>Nest</span></h1>
  <p class="abs hero-sub">Eerspiciatis unde omnis iste natus error</p>
  <a class="abs btn hero-btn" href="#">LEARN MORE <span class="arrow"><svg width="14" height="10" viewBox="0 0 14 10"><path d="M0 5h12M8 1l4 4-4 4" fill="none" stroke="#1b84d0" stroke-width="1.8"/></svg></span></a>
  <div class="abs slide-arrow" style="left:21px;top:242px"><svg width="18" height="12" viewBox="0 0 18 12"><path d="M18 6H2M6 1 1 6l5 5" fill="none" stroke="#fff" stroke-width="1.8"/></svg></div>
  <div class="abs slide-arrow" style="left:1114px;top:242px"><svg width="18" height="12" viewBox="0 0 18 12"><path d="M0 6h16M12 1l5 5-5 5" fill="none" stroke="#fff" stroke-width="1.8"/></svg></div>
  <div class="abs dots"><span></span><span class="on"></span><span></span></div>
  <svg class="abs" style="left:0;top:530px" width="1200" height="92" viewBox="0 0 1200 92"><polygon points="0,28 1200,82 1200,92 0,92" fill="var(--cyan)"/><polygon points="0,28 0,92 1200,92" fill="var(--cyan)"/></svg>
</section>

<!-- About -->
<section>
  <div class="photo about-photo" role="img" aria-label="Advisor meeting with a couple reviewing loan documents"></div>
  <div class="abs about-tab"></div>
  <h2 class="abs serif-title" style="left:602px;top:808px;font-size:38px">ABOUT US</h2>
  <span class="abs underline" style="left:602px;top:862px"></span>
  <p class="abs lead" style="left:602px;top:876px;width:490px">Veritatiset quasiarc hitecto beataevitae dictasunt explicaboemo enimipsamia.</p>
  <p class="abs body" style="left:602px;top:946px;width:488px;text-align:justify">Perspiciatis unde omniste natus error sit voluptatem accusantium doloremque laudantium totamrem aperiam, eaquepisa quaeabillo inventore veritatisetquasi architecto beatae vitaedictasunt explica boemo enim ipsam voluptatemq.</p>
  <ul class="abs ticks" style="left:602px;top:1060px">
    <li>Perspiciatis unde omniste natus error sit voluptatem</li>
    <li>Sasrorsit voluptatem accusantium doloremque laudantiu</li>
    <li>Kaoptatem accusantium doloremque laudantium</li>
  </ul>
</section>

<!-- Services -->
<section class="abs services">
  <svg class="abs" style="left:0;top:0" width="1200" height="64" viewBox="0 0 1200 64"><polygon points="0,0 1200,0 1200,64" fill="var(--cyan)"/></svg>
  <h2 class="abs serif-title" style="left:0;width:1200px;text-align:center;top:80px;font-size:38px">WHAT WE DO</h2>
  <span class="abs underline" style="left:569px;top:134px"></span>

  <article class="card" style="left:110px;top:175px">
    <div class="card-photo" role="img" aria-label="Family sitting together under a cardboard roof at home" style="background:linear-gradient(135deg,#cdb9a3,#8a7563)"></div>
    <div class="icon"><svg width="30" height="28" viewBox="0 0 30 28"><path d="M3 14 15 3l12 11M7 11v15h16V11M12 26v-8h6v8" fill="none" stroke="#fff" stroke-width="2"/></svg></div>
    <h3>Mortgages/home Loans</h3>
    <p>Perspiciatis unde omniste natus errorsit voluptatem accusantium doloremque</p>
    <a class="more" href="#">Learn More <span class="mini-arrow"><svg width="12" height="9" viewBox="0 0 12 9"><path d="M0 4.5h10M7 1l3.5 3.5L7 8" fill="none" stroke="#fff" stroke-width="1.6"/></svg></span></a>
  </article>
  <article class="card" style="left:446px;top:175px">
    <div class="card-photo" role="img" aria-label="Smiling man standing beside a new car in a showroom" style="background:linear-gradient(135deg,#c9ccd0,#6f7379)"></div>
    <div class="icon"><svg width="34" height="20" viewBox="0 0 34 20"><path d="M2 13v-3l5-1 4-5h11l5 5 5 1v3zM8 16a2.5 2.5 0 1 0 .1 0M26 16a2.5 2.5 0 1 0 .1 0" fill="none" stroke="#fff" stroke-width="1.8"/></svg></div>
    <h3>Car Loans</h3>
    <p>Perspiciatis unde omniste natus errorsit voluptatem accusantium doloremque</p>
    <a class="more" href="#">Learn More <span class="mini-arrow"><svg width="12" height="9" viewBox="0 0 12 9"><path d="M0 4.5h10M7 1l3.5 3.5L7 8" fill="none" stroke="#fff" stroke-width="1.6"/></svg></span></a>
  </article>
  <article class="card" style="left:780px;top:175px">
    <div class="card-photo" role="img" aria-label="Business people exchanging cash across an office desk" style="background:linear-gradient(135deg,#5b5f63,#b7b1a7)"></div>
    <div class="icon"><svg width="30" height="28" viewBox="0 0 30 28"><circle cx="15" cy="7" r="3.5" fill="none" stroke="#fff" stroke-width="1.8"/><circle cx="7" cy="10" r="2.8" fill="none" stroke="#fff" stroke-width="1.6"/><circle cx="23" cy="10" r="2.8" fill="none" stroke="#fff" stroke-width="1.6"/><path d="M3 22c0-5 8-6 12-6s12 1 12 6" fill="none" stroke="#fff" stroke-width="1.8"/></svg></div>
    <h3>Commercial Loans</h3>
    <p>Perspiciatis unde omniste natus errorsit voluptatem accusantium doloremque</p>
    <a class="more" href="#">Learn More <span class="mini-arrow"><svg width="12" height="9" viewBox="0 0 12 9"><path d="M0 4.5h10M7 1l3.5 3.5L7 8" fill="none" stroke="#fff" stroke-width="1.6"/></svg></span></a>
  </article>

  <article class="card" style="left:110px;top:556px">
    <div class="card-photo" role="img" aria-label="Two advisors shaking hands across a table" style="background:linear-gradient(135deg,#3d3a36,#8f8072)"></div>
    <div class="icon"><svg width="26" height="28" viewBox="0 0 26 28"><rect x="4" y="3" width="18" height="22" rx="2" fill="none" stroke="#fff" stroke-width="1.8"/><path d="M8 9h10M8 14h10M8 19h6" stroke="#fff" stroke-width="1.6"/></svg></div>
    <h3>SMSF Loans</h3>
    <p>Perspiciatis unde omniste natus errorsit voluptatem accusantium doloremque</p>
    <a class="more" href="#">Learn More <span class="mini-arrow"><svg width="12" height="9" viewBox="0 0 12 9"><path d="M0 4.5h10M7 1l3.5 3.5L7 8" fill="none" stroke="#fff" stroke-width="1.6"/></svg></span></a>
  </article>
  <article class="card" style="left:446px;top:556px">
    <div class="card-photo" role="img" aria-label="Team working with documents and laptops around a table" style="background:linear-gradient(135deg,#2f3440,#7c8590)"></div>
    <div class="icon"><svg width="28" height="26" viewBox="0 0 28 26"><path d="M3 24h22M6 22v-7M11 22V11M16 22V14M21 22V7M5 12l6-5 5 4 7-7" fill="none" stroke="#fff" stroke-width="1.8"/></svg></div>
    <h3>Business Loans</h3>
    <p>Perspiciatis unde omniste natus errorsit voluptatem accusantium doloremque</p>
    <a class="more" href="#">Learn More <span class="mini-arrow"><svg width="12" height="9" viewBox="0 0 12 9"><path d="M0 4.5h10M7 1l3.5 3.5L7 8" fill="none" stroke="#fff" stroke-width="1.6"/></svg></span></a>
  </article>
  <article class="card" style="left:780px;top:556px">
    <div class="card-photo" role="img" aria-label="Bright open office with people seated at desks" style="background:linear-gradient(135deg,#dfe3e3,#7e8784)"></div>
    <div class="icon"><svg width="24" height="26" viewBox="0 0 24 26"><circle cx="12" cy="8" r="5" fill="none" stroke="#fff" stroke-width="1.8"/><path d="M3 24c0-6 4-9 9-9s9 3 9 9z" fill="none" stroke="#fff" stroke-width="1.8"/></svg></div>
    <h3>Personal Loans</h3>
    <p>Perspiciatis unde omniste natus errorsit voluptatem accusantium doloremque</p>
    <a class="more" href="#">Learn More <span class="mini-arrow"><svg width="12" height="9" viewBox="0 0 12 9"><path d="M0 4.5h10M7 1l3.5 3.5L7 8" fill="none" stroke="#fff" stroke-width="1.6"/></svg></span></a>
  </article>
</section>

<!-- Why choose us -->
<section>
  <div class="photo" role="img" aria-label="Couple reviewing a paper receipt together at home" style="left:610px;top:2226px;width:590px;height:557px;background:linear-gradient(135deg,#8d8a84,#4a4640 55%,#2b2d36)"></div>
  <h2 class="abs serif-title" style="left:114px;top:2302px;font-size:38px">WHY CHOOSE US</h2>
  <span class="abs underline" style="left:114px;top:2356px"></span>
  <p class="abs lead" style="left:114px;top:2370px;width:490px">Veritatiset quasiarc hitecto beataevitae dictasunt explicaboemo enimipsamia.</p>
  <p class="abs body" style="left:114px;top:2440px;width:486px;text-align:justify">Perspiciatis unde omniste natus error sit voluptatem accusantium doloremque laudantium totamrem aperiam, eaquepisa quaeabillo inventore veritatisetquasi architecto beatae vitaedictasunt explica boemo enim ipsam voluptatemq.</p>
  <ul class="abs ticks" style="left:114px;top:2555px">
    <li>Perspiciatis unde omniste natus error sit voluptatem</li>
    <li>Sasrorsit voluptatem accusantium doloremque laudantiu</li>
    <li>Kaoptatem accusantium doloremque laudantium</li>
  </ul>
  <a class="abs btn" href="#" style="left:112px;top:2654px;width:168px;height:42px;padding-left:20px;font-size:13px;clip-path:polygon(0 0,100% 0,94% 100%,0 100%)">LEARN MORE <span class="arrow"><svg width="14" height="10" viewBox="0 0 14 10"><path d="M0 5h12M8 1l4 4-4 4" fill="none" stroke="#1b84d0" stroke-width="1.8"/></svg></span></a>
</section>

<!-- Blog -->
<section>
  <h2 class="abs serif-title" style="left:0;width:1200px;text-align:center;top:2858px;font-size:38px">OUR BLOG</h2>
  <span class="abs underline" style="left:569px;top:2912px"></span>
  <div class="abs circle-nav" style="left:41px;top:3120px"><svg width="18" height="12" viewBox="0 0 18 12"><path d="M18 6H2M6 1 1 6l5 5" fill="none" stroke="#1a4f86" stroke-width="1.8"/></svg></div>
  <div class="abs circle-nav" style="left:1099px;top:3120px"><svg width="18" height="12" viewBox="0 0 18 12"><path d="M0 6h16M12 1l5 5-5 5" fill="none" stroke="#1a4f86" stroke-width="1.8"/></svg></div>
  <article class="post" style="left:138px;top:2946px">
    <div class="post-photo" role="img" aria-label="Hands pointing at financial charts on paper and a screen" style="background:linear-gradient(135deg,#e8ecef,#8a99a8 60%,#394654)"></div>
    <h3>Jakmnis iste natus error accusan tium doloremque</h3>
    <p>Perspicia tisunde omniste natus errorsit voluptatem accusantium doloremque laudantium.</p>
    <div class="date">March 22, 2022, Sunday</div>
    <a class="btn" href="#">Learn More <svg width="16" height="10" viewBox="0 0 16 10"><path d="M0 5h14M10 1l4 4-4 4" fill="none" stroke="#fff" stroke-width="1.6"/></svg></a>
  </article>
  <article class="post" style="left:620px;top:2946px">
    <div class="post-photo" role="img" aria-label="Desk with tablet, laptop and printed financial reports" style="background:linear-gradient(135deg,#2e3640,#77828c 60%,#c2c8cc)"></div>
    <h3>Jakmnis iste natus error accusan tium doloremque</h3>
    <p>Perspicia tisunde omniste natus errorsit voluptatem accusantium doloremque laudantium.</p>
    <div class="date">March 22, 2022, Sunday</div>
    <a class="btn" href="#">Learn More <svg width="16" height="10" viewBox="0 0 16 10"><path d="M0 5h14M10 1l4 4-4 4" fill="none" stroke="#fff" stroke-width="1.6"/></svg></a>
  </article>
</section>

<!-- Contact -->
<section class="abs contact">
  <svg class="abs" style="left:0;top:0" width="1200" height="64" viewBox="0 0 1200 64"><polygon points="0,0 1200,0 1200,64" fill="var(--cyan)"/></svg>
</section>
<div class="photo contact-photo" role="img" aria-label="Faded desk with analysis charts and a pen"></div>
<section>
  <h2 class="abs serif-title" style="left:0;width:1200px;text-align:center;top:3578px;font-size:38px">CONTACT US</h2>
  <span class="abs underline" style="left:569px;top:3632px"></span>
  <p class="abs" style="left:170px;top:3650px;width:860px;text-align:center;font-size:18px;line-height:1.5;color:#555">Perspiciatis undeomnis istenatus errorsit voluptatem accusantium doloremque laudantium totamrem aperiameaque ipsaquae abillo inventore veritatist.</p>
  <div class="field" style="left:234px;top:3730px;width:357px;height:42px"><svg width="11" height="12" viewBox="0 0 11 12"><circle cx="5.5" cy="3" r="3" fill="#1b84d0"/><path d="M0 12c0-4 2.5-5.5 5.5-5.5S11 8 11 12z" fill="#1b84d0"/></svg>FIRST NAME</div>
  <div class="field" style="left:607px;top:3730px;width:358px;height:42px"><svg width="11" height="12" viewBox="0 0 11 12"><circle cx="5.5" cy="3" r="3" fill="#1b84d0"/><path d="M0 12c0-4 2.5-5.5 5.5-5.5S11 8 11 12z" fill="#1b84d0"/></svg>LAST NAME</div>
  <div class="field" style="left:234px;top:3793px;width:357px;height:42px"><svg width="14" height="10" viewBox="0 0 14 10"><rect width="14" height="10" fill="#1b84d0"/><path d="M0 0l7 6 7-6" fill="none" stroke="#fff"/></svg>EMAIL</div>
  <div class="field" style="left:607px;top:3793px;width:358px;height:42px"><svg width="12" height="12" viewBox="0 0 24 24"><path fill="#1b84d0" d="M6.6 10.8a15 15 0 0 0 6.6 6.6l2.2-2.2c.3-.3.7-.4 1-.2 1.1.4 2.3.6 3.6.6.6 0 1 .4 1 1V20c0 .6-.4 1-1 1A17 17 0 0 1 3 4c0-.6.4-1 1-1h3.5c.6 0 1 .4 1 1 0 1.3.2 2.5.6 3.6.1.3 0 .7-.2 1z"/></svg>PHONE</div>
  <div class="field msg" style="left:234px;top:3855px;width:731px;height:130px"><svg width="12" height="12" viewBox="0 0 12 12"><path d="M1 1l10 10" stroke="#1b84d0" stroke-width="2"/></svg>MESSAGE</div>
  <a class="abs btn submit" href="#">SUBMIT <span class="arrow"><svg width="14" height="10" viewBox="0 0 14 10"><path d="M0 5h12M8 1l4 4-4 4" fill="none" stroke="#1b84d0" stroke-width="1.8"/></svg></span></a>
  <svg class="abs" style="left:0;top:4126px" width="1200" height="68" viewBox="0 0 1200 68"><polygon points="0,0 1200,58 1200,68 0,68" fill="var(--cyan)"/></svg>
</section>

<!-- Footer -->
<footer class="abs footer">
  <div class="brand">BorrowNest</div>
  <div class="fcol" style="left:410px"><h4>QUICK LINKS</h4><span class="bar"></span><a href="#">HOME</a><a href="#">ABOUT US</a><a href="#">OUR SERVICES</a><a href="#">OUR TEAM</a><a href="#">CONTACT US</a></div>
  <div class="fcol" style="left:585px"><h4>LINKS</h4><span class="bar"></span><a href="#">COPYRIGHT</a><a href="#">LEGAL</a><a href="#">PRIVACY</a><a href="#">ACCESSIBILITY</a><a href="#">SITEMAP</a></div>
  <div class="fcol" style="left:756px"><h4>SUPPORT</h4><span class="bar"></span><a href="#">TEAM</a><a href="#">ABOUT US</a><a href="#">CAREERS</a><a href="#">OUR VALUES</a></div>
  <div class="fcol" style="left:900px"><h4>CONTACT US</h4><span class="bar"></span>
    <div class="finfo"><svg width="12" height="16" viewBox="0 0 12 16" style="margin-top:12px"><path d="M6 0a6 6 0 0 0-6 6c0 4.5 6 10 6 10s6-5.5 6-10a6 6 0 0 0-6-6zm0 8.5A2.5 2.5 0 1 1 6 3.5a2.5 2.5 0 0 1 0 5z" fill="#1b84d0"/></svg><div><small>Address</small>48 Harlow Street,<br>Texas, USA</div></div>
    <div class="finfo"><svg width="12" height="12" viewBox="0 0 24 24" style="margin-top:12px"><path fill="#1b84d0" d="M6.6 10.8a15 15 0 0 0 6.6 6.6l2.2-2.2c.3-.3.7-.4 1-.2 1.1.4 2.3.6 3.6.6.6 0 1 .4 1 1V20c0 .6-.4 1-1 1A17 17 0 0 1 3 4c0-.6.4-1 1-1h3.5c.6 0 1 .4 1 1 0 1.3.2 2.5.6 3.6.1.3 0 .7-.2 1z"/></svg><div><small>Phone</small>+1 (555) 204 7719</div></div>
    <div class="finfo"><svg width="13" height="10" viewBox="0 0 14 10" style="margin-top:12px"><rect width="14" height="10" fill="#1b84d0"/><path d="M0 0l7 6 7-6" fill="none" stroke="#fff"/></svg><div><small>Email</small>hello@borrownest.mail</div></div>
  </div>
  <div class="fsocial"><span></span><span></span><span></span></div>
  <div class="to-top"><svg width="14" height="10" viewBox="0 0 14 10"><path d="M1 8l6-6 6 6" fill="none" stroke="#fff" stroke-width="2"/></svg></div>
  <div class="fline"></div>
  <div class="copy">©2022. All rights reserved.</div>
</footer>

</body>
</html>
```